Business Card Design

We are a company that provides stump grinding services for residential and commercial clients. Looking for a simple business card design that may have some type of graphic on the card that will tie in with the Tamsen name(Grizzly Bear, Paw Print, etc) . Possibly some foliage wrapping around part of the card? Would like to have a simple design that stands out because it is unique. We are working on getting the website set up and there is a simple graphic on the top of the page that came to mind when I mentioned the leaves.

Industry/Entity Type

Business

Contact Information for Business Card

Tamsen Stump Grinding 303-257-4788KodiakStumps.Com

Font styles to use
Serif

Requirements
Must have
• Business name
• Website Address
• Phone Number
Nice to have
• Graphics that would be associated with a Tamsen bear.
Should not have
• Nothing frilly

```html
<!DOCTYPE html>
<html lang="en">
<head>
<meta charset="utf-8">
<title>Tamsen Stump Grinding — Business Card</title>
<link rel="stylesheet" href="https://fonts.googleapis.com/css2?family=Cinzel:wght@400;500&family=Open+Sans:wght@400&display=swap">
<style>
  :root {
    --backdrop: #141414;
    --card-front: #f4f4f4;
    --card-back: #f8f8f7;
    --ink: #111111;
    --ink-soft: #8f8f8f;
    --mark-faint: #e4e4e3;
  }
  * { box-sizing: border-box; margin: 0; padding: 0; }
  html, body { width: 1200px; height: 900px; overflow: hidden; }
  body { background: var(--backdrop); position: relative; }

  .card {
    position: absolute;
    top: 185px;
    height: 490px;
    border-radius: 12px;
    text-align: center;
    font-family: "Cinzel", "Times New Roman", serif;
    overflow: hidden;
  }
  .card--front { left: 299px; width: 301px; background: var(--card-front); }
  .card--back  { left: 645px; width: 305px; background: var(--card-back); }

  .brand-mark {
    position: absolute;
    left: 0; right: 0;
    color: var(--ink);
    font-weight: 500;
  }
  .card--front .brand-mark { top: 58px; font-size: 36px; letter-spacing: 1px; }
  .card--back .brand-mark {
    top: 225px;
    font-size: 66px;
    color: var(--mark-faint);
    letter-spacing: 2px;
  }

  .company-name {
    position: absolute;
    left: 0; right: 0;
    color: var(--ink);
    font-size: 27px;
    font-weight: 400;
    letter-spacing: 0.5px;
    white-space: nowrap;
  }
  .company-trade {
    position: absolute;
    left: 0; right: 0;
    color: var(--ink-soft);
    font-size: 24px;
    font-weight: 400;
    letter-spacing: 9px;
    padding-left: 9px;
  }
  .card--front .company-name  { top: 133px; }
  .card--front .company-trade { top: 170px; }
  .card--back  .company-name  { top: 373px; }
  .card--back  .company-trade { top: 410px; }

  .contact {
    position: absolute;
    left: 0; right: 0;
    top: 394px;
    list-style: none;
    font-family: "Open Sans", Arial, sans-serif;
    font-size: 13px;
    color: var(--ink);
    line-height: 20px;
  }
  .contact li { display: flex; justify-content: center; align-items: center; gap: 5px; }
  .contact svg { width: 11px; height: 11px; fill: none; stroke: var(--ink); stroke-width: 1.6; }
  .contact .icon-phone { fill: var(--ink); stroke: none; }
</style>
</head>
<body>
  <section class="card card--front" aria-label="Card front">
    <div class="brand-mark">Tamsen</div>
    <h1 class="company-name">TAMSEN STUMP</h1>
    <p class="company-trade">GRINDING</p>
    <ul class="contact">
      <li>
        <svg class="icon-phone" viewBox="0 0 12 12" aria-hidden="true"><path d="M1 4c0-2 2-3 5-3s5 1 5 3v1H8V4H4v1H1zM3 6h6l2 4v1H1v-1zM6 7.2a1.3 1.3 0 1 0 0 2.6a1.3 1.3 0 1 0 0-2.6z"/></svg>
        <span>303-555-0146</span>
      </li>
      <li>
        <svg viewBox="0 0 12 12" aria-hidden="true"><path d="M5 7l2-2M4.5 5.5l-2 2a1.6 1.6 0 0 0 2 2l2-2M7.5 6.5l2-2a1.6 1.6 0 0 0-2-2l-2 2"/></svg>
        <span>TamsenStumps.Com</span>
      </li>
    </ul>
  </section>

  <section class="card card--back" aria-label="Card back">
    <div class="brand-mark" aria-hidden="true">Tamsen</div>
    <h2 class="company-name">TAMSEN STUMP</h2>
    <p class="company-trade">GRINDING</p>
  </section>
</body>
</html>
```